Modern design company business card design

We are a design oriented construction firm. The owner is an architect and licensed General Contractor and accomplished furniture designer. We do new home construction and large scale remodeling and office design. We would like a design for our new business cards that is clean and modern, but relatable. We like the bright green color of our logo mixed with different shades of grey. We're also open to reinterpreting the logo.

Target Market(s)

Potential design clients,
Construction clients

Industry/Entity Type

Architecture

Contact Information for Business Card

Tall Maple Design | Build Inc. (optional with logo, Inc. optional)Jeffrey MorganOwner (optional)317.555.0148 cell317.431.8056 officejmorgan@greensquareinc.comwww.greensquareinc.com

Font styles to use
Sans Serif
Other font styles liked:
• Avenir

Requirements
Nice to have
• I like designs that have some continuity between the front and back, i.e. similar layouts or graphic elements that wrap around the card. I tend to prefer horizontal over vertical, but that's not a have to. I also tend to prefer white or recycled paper.

```html
<!DOCTYPE html>
<html lang="en">
<head>
<meta charset="utf-8">
<title>Tall Maple Design | Build – Business Card</title>
<link rel="stylesheet" href="https://fonts.googleapis.com/css2?family=Jost:wght@400&display=swap">
<style>
  :root {
    --backdrop: #3b3b3b;
    --card-white: #ffffff;
    --leaf-light: #c5dc6a;
    --leaf-mid: #b4d764;
    --leaf-deep: #78c557;
    --ink-dark: #4a4a4a;
    --ink-soft: #7a7a7a;
  }
  html, body {
    margin: 0;
    padding: 0;
    width: 1105px;
    height: 1200px;
    overflow: hidden;
    background: var(--backdrop);
  }
  .canvas {
    position: relative;
    width: 1105px;
    height: 1200px;
  }
  .business-card {
    position: absolute;
    left: 102px;
    top: 343px;
    width: 900px;
    height: 514px;
    background: var(--card-white);
    font-family: "Jost", "Futura", sans-serif;
    overflow: hidden;
  }
  .color-block {
    position: absolute;
    left: 0;
    top: 0;
    width: 529px;
    height: 434px;
    background: linear-gradient(to bottom,
      var(--leaf-light) 0%,
      var(--leaf-light) 58%,
      var(--leaf-mid) 74%,
      var(--leaf-deep) 100%);
  }
  .contact-info {
    position: absolute;
    left: 38px;
    top: 28px;
    color: var(--ink-dark);
  }
  .person-name {
    margin: 0;
    font-size: 39px;
    font-weight: 400;
    line-height: 1;
    text-transform: uppercase;
    letter-spacing: 0.2px;
  }
  .person-title {
    margin: 8px 0 0;
    font-size: 27px;
    font-weight: 400;
    line-height: 1;
    text-transform: uppercase;
  }
  .contact-list {
    list-style: none;
    margin: 20px 0 0;
    padding: 0;
  }
  .contact-item {
    display: flex;
    align-items: center;
    height: 34.5px;
    font-size: 24px;
  }
  .contact-item.is-small { font-size: 22px; }
  .contact-icon {
    width: 20px;
    height: 20px;
    margin-right: 11px;
    fill: var(--ink-dark);
    flex: none;
  }
  .company-name {
    position: absolute;
    right: 43px;
    bottom: 44px;
    margin: 0;
    font-size: 28px;
    font-weight: 400;
    line-height: 1;
    color: var(--ink-soft);
    text-align: right;
    white-space: nowrap;
  }
</style>
</head>
<body>
<div class="canvas">
  <section class="business-card">
    <div class="color-block"></div>

    <div class="contact-info">
      <h1 class="person-name">Dennis Holloway</h1>
      <p class="person-title">Owner</p>
      <ul class="contact-list">
        <li class="contact-item">
          <svg class="contact-icon" viewBox="0 0 20 20" aria-hidden="true"><path d="M4 1.5l3.2 3.4-1.6 2.3c1 2.4 2.8 4.3 5.2 5.3l2.3-1.6 3.4 3.2-1.6 3.4C8 17 3 12 .6 3.1z"/></svg>
          317.555.0148
        </li>
        <li class="contact-item">
          <svg class="contact-icon" viewBox="0 0 20 20" aria-hidden="true"><path d="M5 0h10a1.5 1.5 0 0 1 1.5 1.5v17A1.5 1.5 0 0 1 15 20H5a1.5 1.5 0 0 1-1.5-1.5v-17A1.5 1.5 0 0 1 5 0zm1 2.5v13h8v-13zM10 16.5a1.2 1.2 0 1 0 0 2.4 1.2 1.2 0 0 0 0-2.4z"/></svg>
          317.555.0172
        </li>
        <li class="contact-item is-small">
          <svg class="contact-icon" viewBox="0 0 20 20" aria-hidden="true"><path d="M10 1a9 9 0 1 0 0 18 9 9 0 0 0 0-18zm0 2a7 7 0 0 1 6.5 4.4H13l-1.4 1.8 1.6 2.4-1.2 3.6-2-.6.3-3.2-2.6-1.8.6-2.6L7 5.1A7 7 0 0 1 10 3z"/></svg>
          www.tallmapleinc.example
        </li>
        <li class="contact-item is-small">
          <svg class="contact-icon" viewBox="0 0 20 20" aria-hidden="true"><path d="M1 4h18v12H1zm2 2v.4l7 4.6 7-4.6V6zm0 2.8V14h14V8.8l-7 4.6z"/></svg>
          dholloway@tallmapleinc.example
        </li>
      </ul>
    </div>

    <p class="company-name">Tall Maple Design | Build Inc.</p>
  </section>
</div>
</body>
</html>
```